Home Staging Company needs business card design

We're a home staging company called Brightly Settled Home Staging. We would like a business card design that includes aqua and gray. Our current logo of house within chair is fine but I find we almost always use the logo in one color. I'll upload images of front and back of our current card and our logo. Note that we have dropped "Solutions" from our company name and don't want to include it on the card.

Target Market(s)

Realtors and homeowners - people interested in selling their homes

Contact Information for Business Card

Marisol Thistlewood
Brightly Settled Home Staging
757-555-0193
www.brightlysettled.com
marisol@brightlysettled.com

Font styles to use
Serif
Script

Requirements
Must have
• My logo and contact details
• UPDATE***
• I forgot to say that the company name should be included on the front of the card somehow.

```html
<!DOCTYPE html>
<html lang="en">
<head>
<meta charset="utf-8">
<title>Brightly Settled Home Staging — Business Card</title>
<link rel="stylesheet" href="https://fonts.googleapis.com/css2?family=Playfair+Display:wght@700&family=Questrial&display=swap">
<style>
  :root {
    --backdrop: #3b3b3d;
    --card: #1f1f21;
    --aqua: #55b8c5;
    --white: #ffffff;
    --muted: #d9d9d9;
    --shadow: rgba(0, 0, 0, 0.45);
  }
  * { box-sizing: border-box; margin: 0; padding: 0; }
  html, body {
    width: 799px; height: 1200px; overflow: hidden;
    background: var(--backdrop);
  }
  .sheet {
    width: 799px; height: 1200px;
    display: flex; flex-direction: column;
    align-items: center; justify-content: center; gap: 90px;
  }
  .card {
    position: relative;
    width: 660px; height: 377px;
    background: var(--card);
    border-radius: 4px;
    box-shadow: 0 14px 34px var(--shadow);
    overflow: hidden;
  }
  .brand-name {
    font-family: "Playfair Display", Georgia, serif;
    font-weight: 700;
    color: var(--white);
    line-height: 1.1;
  }
  /* Front */
  .card--front {
    display: flex; flex-direction: column;
    align-items: center; justify-content: center; gap: 22px;
  }
  .brand-dot {
    width: 96px; height: 96px; border-radius: 50%;
    background: var(--aqua);
  }
  .card--front .brand-name { font-size: 38px; text-align: center; }
  .card--front .brand-name span { display: block; font-size: 22px; letter-spacing: 0.42em; margin-top: 6px; }
  /* Back */
  .card--back .brand-name {
    position: absolute; left: 40px; top: 36px;
    font-size: 30px;
  }
  .card--back .brand-name span { display: block; font-size: 16px; letter-spacing: 0.42em; margin-top: 6px; }
  .accent-circle {
    position: absolute; right: -120px; bottom: -150px;
    width: 400px; height: 400px; border-radius: 50%;
    background: var(--aqua);
  }
  .contact {
    position: absolute; left: 40px; top: 176px;
    font-family: "Questrial", Arial, sans-serif;
    color: var(--white);
  }
  .contact__name { font-size: 23px; }
  .contact__title { font-size: 13px; color: var(--muted); margin-top: 3px; margin-bottom: 16px; }
  .contact__list { list-style: none; font-size: 14px; }
  .contact__list li { display: flex; align-items: center; gap: 10px; margin-bottom: 6px; }
  .contact__list svg { width: 13px; height: 13px; fill: var(--aqua); flex: none; }
</style>
</head>
<body>
<main class="sheet">
  <section class="card card--front" aria-label="Card front">
    <div class="brand-dot" aria-hidden="true"></div>
    <p class="brand-name">Brightly Settled<span>HOME STAGING</span></p>
  </section>

  <section class="card card--back" aria-label="Card back">
    <p class="brand-name">Brightly Settled<span>HOME STAGING</span></p>
    <div class="contact">
      <p class="contact__name">Marisol Thistlewood</p>
      <p class="contact__title">Managing Director</p>
      <ul class="contact__list">
        <li>
          <svg viewBox="0 0 16 16" aria-hidden="true"><path d="M3 1h3l1.5 4-2 1.2a9 9 0 0 0 4.3 4.3L11 8.5l4 1.5v3a2 2 0 0 1-2 2A12 12 0 0 1 1 3a2 2 0 0 1 2-2z"/></svg>
          757-555-0193
        </li>
        <li>
          <svg viewBox="0 0 16 16" aria-hidden="true"><path d="M8 0a8 8 0 1 0 0 16A8 8 0 0 0 8 0zm5.9 7h-2.5a12 12 0 0 0-1-4.6A6 6 0 0 1 13.9 7zM8 2c.8 1 1.4 2.8 1.5 5h-3C6.6 4.8 7.2 3 8 2zM5.6 2.4A12 12 0 0 0 4.6 7H2.1a6 6 0 0 1 3.5-4.6zM2.1 9h2.5a12 12 0 0 0 1 4.6A6 6 0 0 1 2.1 9zM8 14c-.8-1-1.4-2.8-1.5-5h3c-.1 2.2-.7 4-1.5 5zm2.4-.4a12 12 0 0 0 1-4.6h2.5a6 6 0 0 1-3.5 4.6z"/></svg>
          www.brightlysettled.com
        </li>
        <li>
          <svg viewBox="0 0 16 16" aria-hidden="true"><path d="M0 3h16v10H0zM1.5 4.5v.3L8 9l6.5-4.2v-.3z"/></svg>
          marisol@brightlysettled.com
        </li>
      </ul>
    </div>
    <div class="accent-circle" aria-hidden="true"></div>
  </section>
</main>
</body>
</html>
```